Demolition Company Billboard Design 13 feet wide 15 feet high

This is my first billboard on a busy road. I want it to be professional but with some eye catching flair that matches by business which is a demoltion business and also list my services. My company slogan is also

"watch kessel clear the lot"

Target Market(s)

Home Ownerd and General Construction Companies

Industry/Entity Type

construction

Colors
0054AA
0677BA
7BADD7
CADEEF
E8F1F8

Requirements
Must have
• My services listed in the pictures my website and my phone number

```html
<!DOCTYPE html>
<html lang="en">
<head>
<meta charset="utf-8">
<title>Kessel Clearing Billboard</title>
<link href="https://fonts.googleapis.com/css2?family=Oswald:wght@300;400;600&family=Roboto+Condensed:wght@700&display=swap" rel="stylesheet">
<style>
  :root {
    --navy: #1f4b7d;
    --charcoal: #4a4a4c;
    --stripe: #5c5c5e;
    --white: #ffffff;
    --page: #e6e8eb;
    --rubble-dark: #3b3128;
    --rubble-mid: #8a7563;
    --rubble-light: #cfc3b4;
    --machine: #f07a28;
  }
  * { box-sizing: border-box; margin: 0; padding: 0; }
  html, body { width: 1200px; height: 1200px; overflow: hidden; background: var(--page); }
  .billboard {
    position: absolute; left: 120px; top: 40px;
    width: 960px; height: 1120px;
    background: var(--white); overflow: hidden;
    box-shadow: 0 6px 24px rgba(0,0,0,.15);
  }
  .site-photo {
    position: absolute; left: 0; top: 0; width: 960px; height: 720px;
    background:
      radial-gradient(circle at 58% 52%, rgba(255,170,90,.85) 0, rgba(240,122,40,.55) 10%, transparent 28%),
      radial-gradient(ellipse at 50% 85%, var(--rubble-light) 0, transparent 55%),
      linear-gradient(180deg, var(--rubble-dark) 0%, var(--rubble-mid) 55%, var(--rubble-light) 100%);
  }
  .bands { position: absolute; left: 0; top: 0; }
  .brand-mark {
    position: absolute; left: 40px; top: 445px;
    width: 190px; height: 190px; border-radius: 50%;
    background: var(--navy); border: 10px solid var(--white);
    display: flex; align-items: center; justify-content: center;
    font-family: "Oswald", sans-serif; font-weight: 400;
    font-size: 46px; color: var(--white); letter-spacing: 1px;
  }
  .slogan {
    position: absolute; left: 0; width: 960px; top: 660px;
    text-align: center; color: var(--white);
    font-family: "Oswald", sans-serif; font-weight: 600;
    font-size: 66px; line-height: 1; letter-spacing: -.5px;
  }
  .services {
    position: absolute; left: 95px; top: 752px; width: 780px; height: 118px;
    background: var(--charcoal); border: 4px solid var(--white); border-radius: 22px;
    display: grid; grid-template-columns: 1fr 1fr 1fr; grid-template-rows: 1fr 1fr;
    padding: 12px 26px; align-items: center;
  }
  .service {
    display: flex; align-items: center; gap: 8px;
    color: var(--white); font-family: "Oswald", sans-serif; font-weight: 300; font-size: 27px;
  }
  .service svg { flex: none; }
  .phone {
    position: absolute; left: 0; width: 960px; top: 895px; text-align: center;
    font-family: "Roboto Condensed", sans-serif; font-weight: 700;
    font-size: 132px; line-height: 1; color: var(--navy); letter-spacing: -1px;
  }
  .website {
    position: absolute; left: 0; width: 960px; top: 1045px; text-align: center;
    font-family: "Roboto Condensed", sans-serif; font-weight: 700;
    font-size: 44px; color: var(--navy);
  }
</style>
</head>
<body>
  <main class="billboard">
    <div class="site-photo" role="img" aria-label="Orange excavator working among the rubble of a demolished building"></div>

    <svg class="bands" width="960" height="1120" viewBox="0 0 960 1120" aria-hidden="true">
      <path d="M0,380 C90,560 300,665 520,650 C700,638 860,575 960,480 L960,780 L0,780 Z" fill="var(--navy)"/>
      <path d="M300,630 C420,655 520,650 600,640 C740,622 870,560 960,470" fill="none" stroke="var(--white)" stroke-width="14"/>
      <path d="M330,616 C440,640 530,636 600,626 C740,606 870,546 960,452" fill="none" stroke="var(--stripe)" stroke-width="16"/>
      <path d="M0,365 C40,440 80,495 130,540" fill="none" stroke="var(--white)" stroke-width="8"/>
    </svg>

    <div class="brand-mark">KCL</div>

    <h1 class="slogan">Watch Kessel Clear The Lot</h1>

    <ul class="services">
      <li class="service"><svg width="24" height="26" viewBox="0 0 24 26"><rect x="1.5" y="4.5" width="18" height="19" fill="none" stroke="#fff" stroke-width="2"/><path d="M5 14 L10 20 L22 2" fill="none" stroke="#fff" stroke-width="2.5"/></svg>Room Gut Out</li>
      <li class="service"><svg width="24" height="26" viewBox="0 0 24 26"><rect x="1.5" y="4.5" width="18" height="19" fill="none" stroke="#fff" stroke-width="2"/><path d="M5 14 L10 20 L22 2" fill="none" stroke="#fff" stroke-width="2.5"/></svg>Partial Demolition</li>
      <li class="service"><svg width="24" height="26" viewBox="0 0 24 26"><rect x="1.5" y="4.5" width="18" height="19" fill="none" stroke="#fff" stroke-width="2"/><path d="M5 14 L10 20 L22 2" fill="none" stroke="#fff" stroke-width="2.5"/></svg>Commercial</li>
      <li class="service"><svg width="24" height="26" viewBox="0 0 24 26"><rect x="1.5" y="4.5" width="18" height="19" fill="none" stroke="#fff" stroke-width="2"/><path d="M5 14 L10 20 L22 2" fill="none" stroke="#fff" stroke-width="2.5"/></svg>House Gut Out</li>
      <li class="service"><svg width="24" height="26" viewBox="0 0 24 26"><rect x="1.5" y="4.5" width="18" height="19" fill="none" stroke="#fff" stroke-width="2"/><path d="M5 14 L10 20 L22 2" fill="none" stroke="#fff" stroke-width="2.5"/></svg>Full Demolition</li>
      <li class="service"><svg width="24" height="26" viewBox="0 0 24 26"><rect x="1.5" y="4.5" width="18" height="19" fill="none" stroke="#fff" stroke-width="2"/><path d="M5 14 L10 20 L22 2" fill="none" stroke="#fff" stroke-width="2.5"/></svg>Residental</li>
    </ul>

    <p class="phone">412-555-0187</p>
    <p class="website">www.kesselclearing.com</p>
  </main>
</body>
</html>
```